website design + images

We need a very appealing website design, layout and images for a sales analytics and sales productivity services company based in San Ramon, California. We need a good design for the home page and a template for all other pages (total 2 designs), and images for all inner pages (center column/banner images, and right hand top corner small images). There are about 18 inner pages.
Updates

Our existing website is www.brightvale.com
Our corporate colours are the ones that are there on the website. The logo is also shown. We will be changing the tagline to "accelerating revenue" or equivalent of that.

Please use the document "website for brightvale - template v2.doc" that I just uploaded for any reference to the content, navigation and wireframes. A few more clarifications are provided mainly for the link "Solutions".

Rajesh Kothuri

Hi,
We just uploaded ver 4 of the website template. There is more elaboration provided around the sublinks / sections for Solutions. Pls review and do get back if you need any clarifications.

Rgds
Rajesh Kothuri

Hi all,
We have so far received a few good designs. The designs are more or less on the right track. I would like to urge all of you to use the content and navigation provided in the document attached to our brief "website for brightvale - template v4.doc".  Please DO NOT use the content in our existing website www.brightvale.com . That is very old. We mentioned it only for reference to colour theme and broad details.

We have totally 13 sections in Solutions pages. They may be designed as a tree of links - first level sublinks - second level sublinks or links - first level sublinks and the remaining as sections within the first level sublinks pages. The page design would remain the same for all inner pages except careers. But after finalizing the design for the inner page, we will need images for the different inner pages.

Rgds
Rajesh Kothuri

Hi,
Thank you all for participation and very good designs. We are quite happy with what we have seen. We have now shortlisted about 4 vendors and sending invididual feedback to them for further improvement. We will be finalizing by Monday or Tuesday.  To the vendors who do not get feedback from us, thank you very much for participation. We may still do business in future for some of our other needs. 
The following are the process steps / expectations going forward, 
1. Feedback to the shortlisted designers and inviting improvements.
2. Review of the improved designs and further shortlist & feedback or direct finalization.
3. The design should be in 1024*768
2. Number of page designs = 2 (home page, inner page).
4. Home page design: instead of delivery model and customers, show one link "Why Us".
4. Solutions page design:  We will be needing an image in center column of solutions page that in a nutshell gives all the different types of solutions we provide. The entire set of solutions is in our attached document website for brightvale - template v4 and I am just uploading v5 with more description on sublinks.
5. After selection, we will be needing images for all the solution pages (total 12 pages under solutions + one solutions page), 1 image for Why Us?, 1 for Careers, and 3 for company (about us/ team, core values, ...) = total 18

Rgds
Rajesh Kothuri

Target Market(s)

We are a sales analytics and sales productivity services company. We help B2B companies with: sales planning; sales operations and sales measurement. The characteristics of our customers are:
- B2B medium enterprises (USD 100M- USD 2B in revenue) in the US
- Primary target verticals are: high-tech, engineering and professional services firms
- Our primary target customers titles are VP of Sales or VP of marketing; we could be selling to the CEO at companies with revenues below $200M

Industry/Entity Type

Consulting

Requirements
Must have
• - Clean, uncluttered design
• - Easy navigation; minimum clicks
Nice to have
• We have already built a content management system and wireframes for this site. To the extent possible, it would be great to leverage the wireframe structure we built, provided you don’t have to compromise on the look and feel and navigation of the site. Below is what we currently have as banner sizes and resolutions are:
• Home page banner size: 950 * 250’
• All pages – center top - image size: 558 * 160
• All pages – right hand top image – 175*135’

```html
<!DOCTYPE html>
<html lang="en">
<head>
<meta charset="utf-8">
<title>Brightvale – Home</title>
<link href="https://fonts.googleapis.com/css2?family=Arimo:ital,wght@0,400;0,700;1,400&display=swap" rel="stylesheet">
<style>
:root{
  --page-bg:#f2f2f2;
  --stage-bg:#ececec;
  --white:#ffffff;
  --blue:#0a64b0;
  --blue-dark:#0758a3;
  --green:#3c9a3c;
  --orange:#f5a214;
  --grey-text:#7d7d7d;
  --nav-grey:#8c8c8c;
  --tile-bg:#efefef;
  --shadow:0 3px 4px rgba(0,0,0,.28);
}
*{margin:0;padding:0;box-sizing:border-box}
html,body{width:1200px;height:712px;overflow:hidden}
body{background:var(--page-bg);font-family:"Arimo",Arial,sans-serif;position:relative}
.stage{position:absolute;left:143px;top:131px;width:943px;height:581px;background:var(--stage-bg)}
.header{position:absolute;left:161px;top:0;width:891px;height:99px;background:var(--white)}
.brand{position:absolute;left:23px;top:34px;display:flex;align-items:center;gap:8px}
.brand-dot{width:18px;height:18px;border-radius:50%;background:var(--blue)}
.brand-name{font-size:26px;font-weight:400;color:var(--blue);letter-spacing:2px}
.utility{position:absolute;right:34px;top:14px;font-size:11px;color:var(--nav-grey)}
.nav{position:absolute;top:80px;left:0;width:100%;list-style:none;font-size:10.5px;font-weight:700;color:var(--nav-grey)}
.nav li{position:absolute}
.nav li.active{color:var(--blue)}
.banner{position:absolute;left:161px;top:99px;width:891px;height:235px;box-shadow:var(--shadow);
  background:linear-gradient(90deg,#0862b0 0%,#0a66b2 40%,#4a8fcc 65%,#8fb9e0 100%)}
.banner-photo{position:absolute;right:0;top:0;width:520px;height:235px;
  background:linear-gradient(90deg,rgba(255,255,255,0) 0%,rgba(200,210,215,.35) 70%,rgba(230,225,215,.45) 100%)}
.banner-title{position:absolute;left:22px;top:70px;color:var(--white)}
.banner-title h1{font-size:23px;font-weight:700}
.banner-title p{font-size:16.5px;margin-top:2px}
.panel{position:absolute;top:354px;height:272px;background:var(--white);box-shadow:var(--shadow)}
.panel-main{left:161px;width:629px}
.panel-side{left:808px;width:242px}
.section-head{position:absolute;top:42px;display:flex;justify-content:space-between;font-size:12px;font-weight:700;color:var(--blue);border-bottom:1px solid var(--blue);padding-bottom:1px}
.section-head span.arrow{font-size:14px;line-height:12px}
.intro-head{left:22px;width:246px}
.intro-text{position:absolute;left:23px;top:67px;width:250px;font-size:11.5px;line-height:17px;color:var(--grey-text)}
.intro-text p+p{margin-top:17px}
.read-more{position:absolute;font-size:10px;font-weight:700;color:var(--blue)}
.tile{position:absolute;top:31px;width:103px;height:141px;background:var(--tile-bg)}
.tile-img{height:68px}
.tile h3{font-size:11.5px;font-weight:700;line-height:13px;padding:6px 6px 0}
.t1{left:288px}.t1 .tile-img{background:linear-gradient(180deg,#e4e4e4,#cfd3d8)}.t1 h3{color:var(--blue)}
.t2{left:400px}.t2 .tile-img{background:linear-gradient(180deg,#dcdcdc,#c9cfc4)}.t2 h3{color:var(--green)}
.t3{left:513px}.t3 .tile-img{background:linear-gradient(180deg,#ececec,#e3dccb)}.t3 h3{color:var(--orange)}
.testi-head{left:10px;width:218px}
.quote{position:absolute;left:29px;top:97px;width:205px;font-size:13.5px;font-style:italic;line-height:19px;color:var(--green)}
.author{position:absolute;left:29px;top:201px;font-size:10.5px;font-weight:700;line-height:15px;color:var(--blue)}
.footer{position:absolute;left:161px;top:641px;width:891px;height:32px;background:var(--white);box-shadow:var(--shadow)}
.footer p{position:absolute;right:35px;top:11px;font-size:10.5px;font-style:italic;color:var(--nav-grey)}
</style>
</head>
<body>
<div class="stage"></div>

<header class="header">
  <div class="brand"><span class="brand-dot"></span><span class="brand-name">BRIGHTVALE</span></div>
  <div class="utility">Sitemap | Sign in / Register | Contact us</div>
  <ul class="nav">
    <li class="active" style="left:217px">HOME</li>
    <li style="left:288px">SOLUTIONS</li>
    <li style="left:388px">WHY US?</li>
    <li style="left:473px">DELIVERY</li>
    <li style="left:561px">INDUSTRY VERTICALS</li>
    <li style="left:715px">COMPANY</li>
    <li style="left:807px">CAREERS</li>
  </ul>
</header>

<section class="banner">
  <div class="banner-photo" role="img" aria-label="Relaxed businessman leaning back with feet on a desk beside a laptop under a blue sky"></div>
  <div class="banner-title">
    <h1>Lorem ipsum dolor sit amet.</h1>
    <p>consectetur adipiscing elit.</p>
  </div>
</section>

<section class="panel panel-main">
  <div class="section-head intro-head"><span>INTRODUCTION</span><span class="arrow">&gt;</span></div>
  <div class="intro-text">
    <p>At Brightvale, we deliver solutions to improve sales productivity and marketing effectiveness of high-tech, engineering, and professional services firms.</p>
    <p>Our customers lead corporate marketing, product marketing, channel marketing, sales operations, sales management and IT functions at their organizations.</p>
  </div>
  <div class="read-more" style="left:200px;top:252px">&gt;&gt; read more...</div>

  <div class="tile t1"><div class="tile-img" role="img" aria-label="Calendar grid with blue pins"></div><h3>SALES<br>PLANNING<br>ANALYTICS</h3></div>
  <div class="tile t2"><div class="tile-img" role="img" aria-label="Keyboard with a green support key"></div><h3>SALES<br>OPERATIONS<br>SUPPORT</h3></div>
  <div class="tile t3"><div class="tile-img" role="img" aria-label="Rising growth line on a grid"></div><h3>SALES<br>MEASUREMENT<br>ANALYTICS</h3></div>
</section>

<aside class="panel panel-side">
  <div class="section-head testi-head"><span>CUSTOMER TESTIMONIAL</span><span class="arrow">&gt;</span></div>
  <p class="quote">Aliquam eros leo, pretium at imperdiet id, fringilla at velit. Donec pellentesque mollis massa eu porttitor. Aliquam risus metus, placerat at ornare id</p>
  <p class="author">Name Person<br>Northwind Partners</p>
  <div class="read-more" style="left:150px;top:252px">&gt;&gt; read more...</div>
</aside>

<footer class="footer"><p>© 2008 Brightvale, Inc. | Disclaimer</p></footer>
</body>
</html>
```